Business Card Design Project

We are a construction company in Orange County, CA. We need a two sided business card. We would like the back to be our logo with web URL. Front should included Name, title, address, phone, fax and email address.

our address is
627 West Dorrance Blvd, Suite 308
Anaheim, CA 92718

Our logo files are attached.

Construction

```html
<!DOCTYPE html>
<html lang="en">
<head>
<meta charset="utf-8">
<title>Braxel Business Card</title>
<link href="https://fonts.googleapis.com/css2?family=Source+Sans+3:wght@400;600;700;800&display=swap" rel="stylesheet">
<style>
  :root {
    --brand-blue: #1a4a7e;
    --stripe-grey: #4a4a4c;
    --card-white: #ffffff;
    --backdrop: #e6e6e8;
    --text-light: #ffffff;
  }
  html, body {
    margin: 0;
    padding: 0;
    width: 1200px;
    height: 402px;
    overflow: hidden;
    background: var(--backdrop);
    font-family: "Source Sans 3", sans-serif;
  }
  .stage {
    position: relative;
    width: 1200px;
    height: 402px;
  }
  .card {
    position: absolute;
    top: 56px;
    width: 511px;
    height: 291px;
    border-radius: 18px;
    overflow: hidden;
  }
  .card-front { left: 64px; background: var(--card-white); }
  .card-back  { left: 629px; background: var(--brand-blue); }

  .front-shapes {
    position: absolute;
    inset: 0;
    width: 100%;
    height: 100%;
  }
  .front-shapes .panel  { fill: var(--brand-blue); }
  .front-shapes .stripe { fill: var(--stripe-grey); }

  .wordmark {
    position: absolute;
    margin: 0;
    font-weight: 800;
    letter-spacing: -1px;
    line-height: 1;
  }
  .wordmark-front {
    left: 25px;
    top: 50px;
    font-size: 62px;
    color: var(--brand-blue);
  }
  .wordmark-back {
    left: 0;
    right: 0;
    top: 100px;
    text-align: center;
    font-size: 92px;
    color: var(--text-light);
  }

  .contact {
    position: absolute;
    right: 33px;
    top: 30px;
    text-align: right;
    color: var(--text-light);
    font-size: 13px;
    line-height: 1.3;
  }
  .person-name {
    margin: 0;
    font-size: 16px;
    font-weight: 700;
    line-height: 1.1;
  }
  .person-title {
    margin: 0 0 0;
    font-size: 12px;
  }
  .address {
    margin: 54px 0 0;
    font-style: normal;
  }
  .lines {
    list-style: none;
    margin: 42px 0 0;
    padding: 0;
  }
  .lines li {
    display: flex;
    justify-content: flex-end;
    align-items: center;
    gap: 5px;
    height: 18px;
  }
  .lines li.gap-above { margin-top: 4px; }
  .icon {
    width: 10px;
    height: 10px;
    fill: var(--text-light);
    stroke: none;
  }
</style>
</head>
<body>
<main class="stage">

  <section class="card card-front" aria-label="Card front">
    <svg class="front-shapes" viewBox="0 0 511 291" preserveAspectRatio="none" aria-hidden="true">
      <path class="stripe" d="M284 0 L302 0 C388 88 326 214 146 291 L140 291 C306 210 364 92 284 0 Z"/>
      <path class="panel" d="M306 0 C392 92 332 218 152 291 L511 291 L511 0 Z"/>
    </svg>

    <p class="wordmark wordmark-front">BRAXEL</p>

    <div class="contact">
      <p class="person-name">Your name</p>
      <p class="person-title">Title</p>
      <address class="address">
        627 West Dorrance Blvd<br>
        Suite 308<br>
        Anaheim, CA&nbsp; 92718
      </address>
      <ul class="lines">
        <li>
          <svg class="icon" viewBox="0 0 10 10" aria-label="Phone"><path d="M2 0.5 L3.6 2.6 L2.7 3.7 C3.4 5 4.9 6.5 6.3 7.3 L7.4 6.4 L9.5 8 L8.3 9.5 C4.5 9.2 0.8 5.5 0.5 1.7 Z"/></svg>
          <span>01-234-5678</span>
        </li>
        <li>
          <svg class="icon" viewBox="0 0 10 10" aria-label="Fax"><path d="M2.5 0.5 H7.5 V3 H9.5 V7.5 H7.5 V9.5 H2.5 V7.5 H0.5 V3 H2.5 Z M3.3 6 V8.7 H6.7 V6 Z"/></svg>
          <span>01-234-5678</span>
        </li>
        <li class="gap-above">
          <svg class="icon" viewBox="0 0 10 10" aria-label="Email"><path d="M0.5 2 H9.5 V8.2 H0.5 Z M1.2 2.6 L5 5.4 L8.8 2.6 Z" fill-rule="evenodd"/></svg>
          <span>info@braxelmail.com</span>
        </li>
        <li>
          <svg class="icon" viewBox="0 0 10 10" aria-label="Website"><circle cx="5" cy="5" r="4.5"/><path d="M0.5 4.6 H9.5 V5.4 H0.5 Z" fill="#1a4a7e"/></svg>
          <span>www.braxel.com</span>
        </li>
      </ul>
    </div>
  </section>

  <section class="card card-back" aria-label="Card back">
    <p class="wordmark wordmark-back">BRAXEL</p>
  </section>

</main>
</body>
</html>
```